Global (re)insurance broker needs a business card design

We need a classic business card for our company that is headquartered in SG, with offices in Malaysia and Dubai. We specialise in insurance and reinsurance broking and consultancy for our global clients.

```html
<!DOCTYPE html>
<html lang="en">
<head>
<meta charset="UTF-8">
<title>Vantrell – Business Card</title>
<link href="https://fonts.googleapis.com/css2?family=Open+Sans:wght@400;600;700&display=swap" rel="stylesheet">
<style>
  :root {
    --stage: #2a2a2c;
    --paper: #f4f4ec;
    --brand-blue: #1f3f9a;
    --brand-green: #a9cfa1;
    --green-light: #d6e9cf;
    --ink: #161616;
    --white: #ffffff;
  }
  * { box-sizing: border-box; margin: 0; padding: 0; }
  html, body {
    width: 1200px;
    height: 780px;
    overflow: hidden;
    background: var(--stage);
    font-family: "Open Sans", Arial, sans-serif;
  }
  .canvas {
    width: 1200px;
    height: 780px;
    display: flex;
    align-items: center;
    justify-content: center;
    gap: 40px;
  }
  .card {
    position: relative;
    width: 520px;
    height: 300px;
    overflow: hidden;
    box-shadow: 0 10px 30px rgba(0,0,0,0.45);
  }

  /* Front */
  .card-front { background: var(--paper); }
  .identity {
    position: absolute;
    left: 22px;
    top: 22px;
    padding-left: 14px;
    border-left: 8px solid var(--brand-blue);
  }
  .person-name {
    font-size: 30px;
    font-weight: 700;
    line-height: 1.05;
    color: var(--brand-blue);
    letter-spacing: 0.2px;
  }
  .person-name .surname { color: var(--brand-green); }
  .person-title {
    font-size: 13px;
    font-weight: 400;
    color: var(--ink);
    margin-top: 2px;
  }
  .contact {
    position: absolute;
    left: 30px;
    top: 150px;
    font-size: 13px;
    line-height: 1.4;
    color: var(--ink);
    list-style: none;
  }
  .contact .address { margin-bottom: 2px; }
  .contact li { display: flex; align-items: center; gap: 8px; }
  .contact svg { width: 12px; height: 12px; flex: none; }
  .brand-mark {
    position: absolute;
    right: -22px;
    bottom: 6px;
    transform-origin: right bottom;
    transform: rotate(-90deg) translateX(100%);
    font-size: 118px;
    font-weight: 600;
    line-height: 0.8;
    color: var(--brand-blue);
    letter-spacing: 2px;
    white-space: nowrap;
  }

  /* Back */
  .card-back {
    background: linear-gradient(105deg, var(--brand-green) 0%, #b7d8af 55%, var(--green-light) 100%);
  }
  .pattern-area {
    position: absolute;
    inset: 0;
  }
  .back-brand {
    position: absolute;
    left: 300px;
    top: 196px;
    font-size: 18px;
    font-weight: 600;
    color: var(--white);
    letter-spacing: 1px;
  }
</style>
</head>
<body>
<main class="canvas">

  <section class="card card-front">
    <div class="identity">
      <h1 class="person-name">Mira <span class="surname">Lindqvist</span></h1>
      <p class="person-title">Chief Operating Officer</p>
    </div>

    <ul class="contact">
      <li class="address">28 Harbour Lane, Meridian<br>Tower #08-04, Singapore 048512</li>
      <li>
        <svg viewBox="0 0 12 12"><rect x="3" y="1" width="6" height="10" rx="1.2" fill="none" stroke="#1f3f9a" stroke-width="1.3"/></svg>
        +65 8123 4567
      </li>
      <li>
        <svg viewBox="0 0 12 12"><circle cx="6" cy="6" r="5" fill="#1f3f9a"/><path d="M1 6h10M6 1c2 2.5 2 7.5 0 10M6 1c-2 2.5-2 7.5 0 10" stroke="#f4f4ec" stroke-width="0.8" fill="none"/></svg>
        www.vantrell.com
      </li>
      <li>
        <svg viewBox="0 0 12 12"><rect x="1" y="2.5" width="10" height="7" fill="#1f3f9a"/><path d="M1 2.5l5 4 5-4" stroke="#f4f4ec" stroke-width="0.9" fill="none"/></svg>
        mira@vantrell.com
      </li>
    </ul>

    <div class="brand-mark">VANTRELL</div>
  </section>

  <section class="card card-back">
    <div class="pattern-area" role="img" aria-label="Repeated brand-name pattern in soft green tones"></div>
    <p class="back-brand">VANTRELL</p>
  </section>

</main>
</body>
</html>
```